Simple proffessional BC

I have a logo which I will attach below.
I would like the logo on the front of the card with these details in point form below:
Pre and Post Natal Yoga: Pregnancy Workshops: Hypnobirthing Courses
On the back of the card my details:
Marla Pennick
Facebook page- stretchbelliesbayridgefield
Mobile- 0491 352 718

I like the idea of the card being simple, possibly just the above on a plain coloured (eggshell?) card, a card that is textured.
I am open to suggestion if it appeals!
Thank you and good luck!

Target Market(s)

Pregnant women, 20's-40's

Requirements
Must have
• Simple, compliment logo.
Make logo the feature.
Should not have

• .

```html
<!DOCTYPE html>
<html lang="en">
<head>
<meta charset="utf-8">
<title>Stretch Bellies – Business Card</title>
<link rel="stylesheet" href="https://fonts.googleapis.com/css2?family=Exo+2:wght@400;500;600&display=swap">
<style>
  :root {
    --backdrop-top: #f2f2f3;
    --backdrop-bottom: #c9cacd;
    --card-white: #ffffff;
    --brand-red: #862b2f;
    --brand-orange: #eca43f;
    --ink-dark: #2b2b2b;
    --text-light: #ffffff;
    --card-shadow: rgba(0, 0, 0, 0.22);
  }
  * { margin: 0; padding: 0; box-sizing: border-box; }
  html, body {
    width: 1200px;
    height: 883px;
    overflow: hidden;
  }
  body {
    background: linear-gradient(180deg, var(--backdrop-top), var(--backdrop-bottom));
    font-family: "Exo 2", "Trebuchet MS", sans-serif;
    position: relative;
  }
  .card {
    position: absolute;
    width: 640px;
    height: 366px;
    border-radius: 36px;
    background: var(--card-white);
    overflow: hidden;
    box-shadow: 0 14px 30px var(--card-shadow);
  }
  .card--back { left: 500px; top: 46px; }
  .card--front { left: 60px; top: 470px; }
  .card__shapes { position: absolute; inset: 0; }

  .brand { position: absolute; display: flex; align-items: center; gap: 18px; }
  .brand__dot {
    width: 84px; height: 84px; border-radius: 50%;
    background: var(--brand-orange);
  }
  .brand__name {
    font-size: 38px; font-weight: 500; color: var(--brand-red);
    letter-spacing: 0.5px; white-space: nowrap;
  }
  .card--front .brand { left: 26px; top: 32px; }

  .card--back .brand {
    left: 0; right: 0; top: 70px;
    flex-direction: column; gap: 14px;
  }
  .card--back .brand__dot { width: 80px; height: 80px; }
  .services {
    position: absolute; left: 0; right: 0; top: 232px;
    display: flex; justify-content: center; gap: 22px;
    list-style: none; font-size: 14px; color: var(--brand-red);
  }
  .services li::before { content: "• "; color: var(--brand-orange); }
  .card--back .website {
    position: absolute; left: 0; right: 0; top: 278px; text-align: center;
    font-size: 16px; letter-spacing: 3px; color: var(--ink-dark);
  }

  .holder { position: absolute; right: 40px; text-align: right; color: var(--text-light); }
  .holder__name {
    top: 126px; font-size: 19px; font-weight: 500;
    letter-spacing: 1.5px; text-transform: uppercase;
  }
  .holder__role { top: 172px; font-size: 15px; }
  .card--front .website {
    position: absolute; right: 40px; top: 236px;
    font-size: 16px; letter-spacing: 1px; color: var(--text-light);
  }
  .contact {
    position: absolute; left: 36px; top: 278px;
    list-style: none; color: var(--text-light);
    font-size: 16px; line-height: 22px; letter-spacing: 0.5px;
  }
  .contact__label { font-weight: 600; }
</style>
</head>
<body>

  <section class="card card--back" aria-label="Card back">
    <div class="brand">
      <span class="brand__dot"></span>
      <span class="brand__name">Stretch Bellies</span>
    </div>
    <ul class="services">
      <li>Pre and Post Natal Yoga</li>
      <li>Pregnancy Workshops</li>
      <li>Hypnobirthing Courses</li>
    </ul>
    <p class="website">www.stretchbellies.com</p>
  </section>

  <section class="card card--front" aria-label="Card front">
    <svg class="card__shapes" width="640" height="366" viewBox="0 0 640 366" aria-hidden="true">
      <path d="M0,150 H380 Q394,150 397,136 L399,128 Q402,114 416,114 H640 V366 H0 Z" fill="var(--brand-orange)"/>
      <rect x="0" y="162" width="640" height="204" fill="var(--brand-red)"/>
    </svg>
    <div class="brand">
      <span class="brand__dot"></span>
      <span class="brand__name">Stretch Bellies</span>
    </div>
    <p class="holder holder__name">Marla Pennick</p>
    <p class="holder holder__role">Managing Director</p>
    <p class="website">www.stretchbellies.com</p>
    <ul class="contact">
      <li><span class="contact__label">Mobile</span> 0491 352 718</li>
      <li><span class="contact__label">Facebook</span> stretchbelliesbayridgefield</li>
      <li>hello@stretchbellies.com</li>
    </ul>
  </section>

</body>
</html>
```